German Headhunter/ HR Consultancy needs Business Cards Design

We need a business Card Design for our Company in Stuttgart. We are specialized as Headhunter/ HR Consultancy in Placement of specialist and managers in permanent employment. Please refer to our business logo.

```html
<!DOCTYPE html>
<html lang="en">
<head>
<meta charset="utf-8">
<title>Kernwerk Personalberatung – Business Card</title>
<link href="https://fonts.googleapis.com/css2?family=Montserrat:wght@400;500;700;800&family=Arimo:wght@400&display=swap" rel="stylesheet">
<style>
  :root {
    --brand-blue: #3b55a8;
    --card-white: #ffffff;
    --ink-grey: #4a4a4a;
    --stage: #e9eaee;
  }
  * { margin: 0; padding: 0; box-sizing: border-box; }
  html, body {
    width: 1200px;
    height: 1015px;
    overflow: hidden;
    background: var(--stage);
  }
  .stage {
    position: relative;
    width: 1200px;
    height: 1015px;
  }
  .card {
    position: absolute;
    left: 300px;
    width: 600px;
    height: 343px;
    box-shadow: 0 6px 18px rgba(0,0,0,0.18);
    overflow: hidden;
  }
  .card--front {
    top: 142px;
    background: var(--brand-blue);
    display: flex;
    align-items: center;
    justify-content: center;
  }
  .brand {
    color: var(--card-white);
    font-family: "Montserrat", sans-serif;
    text-align: left;
  }
  .brand__name {
    font-weight: 800;
    font-size: 46px;
    letter-spacing: 4px;
    line-height: 1;
  }
  .brand__tagline {
    font-weight: 800;
    font-size: 19.5px;
    letter-spacing: 2.6px;
    margin-top: 6px;
  }
  .card--back {
    top: 530px;
    background: var(--card-white);
  }
  .back-brand {
    position: absolute;
    right: 44px;
    top: 56px;
    font-family: "Montserrat", sans-serif;
    font-weight: 800;
    font-size: 34px;
    line-height: 1;
    letter-spacing: 3px;
    color: var(--brand-blue);
  }
  .accent-square {
    position: absolute;
    left: 0;
    top: 130px;
    width: 56px;
    height: 50px;
    background: var(--brand-blue);
  }
  .person {
    position: absolute;
    left: 72px;
    top: 130px;
    font-family: "Montserrat", sans-serif;
  }
  .person__name {
    color: var(--brand-blue);
    font-weight: 800;
    font-size: 26px;
    letter-spacing: 0.5px;
    line-height: 1.05;
  }
  .person__role {
    color: var(--ink-grey);
    font-weight: 500;
    font-size: 15px;
    letter-spacing: 1px;
    margin-top: 3px;
  }
  .contacts {
    position: absolute;
    left: 72px;
    top: 200px;
    list-style: none;
    font-family: "Arimo", sans-serif;
    font-size: 17px;
    color: var(--ink-grey);
  }
  .contacts li {
    display: flex;
    align-items: center;
    gap: 8px;
    height: 25px;
  }
  .contacts svg { width: 16px; height: 16px; fill: var(--brand-blue); flex: none; }
  .contacts .highlight { color: var(--brand-blue); }
  .address {
    position: absolute;
    left: 96px;
    top: 288px;
    font-family: "Arimo", sans-serif;
    font-style: normal;
    font-size: 16px;
    line-height: 1.3;
    color: var(--ink-grey);
  }
</style>
</head>
<body>
<main class="stage">
  <section class="card card--front" aria-label="Card front">
    <div class="brand">
      <div class="brand__name">KERNWERK</div>
      <div class="brand__tagline">PERSONALBERATUNG</div>
    </div>
  </section>

  <section class="card card--back" aria-label="Card back">
    <div class="back-brand">KERNWERK</div>
    <div class="accent-square"></div>
    <div class="person">
      <div class="person__name">JONATHAN SMITH</div>
      <div class="person__role">MANAGING DIRECTOR</div>
    </div>
    <ul class="contacts">
      <li>
        <svg viewBox="0 0 24 24" aria-hidden="true"><path d="M6.6 10.8a15 15 0 0 0 6.6 6.6l2.2-2.2c.3-.3.7-.4 1-.2 1.1.4 2.3.6 3.6.6.6 0 1 .4 1 1V20c0 .6-.4 1-1 1A17 17 0 0 1 3 4c0-.6.4-1 1-1h3.5c.6 0 1 .4 1 1 0 1.3.2 2.5.6 3.6.1.3 0 .7-.2 1z"/></svg>
        044-123 456 789
      </li>
      <li>
        <svg viewBox="0 0 24 24" aria-hidden="true"><path d="M2 5h20v14H2zM4 7v.4l8 5 8-5V7zM4 9.8V17h16V9.8l-8 5z"/></svg>
        info@webname.com
      </li>
      <li>
        <svg viewBox="0 0 24 24" aria-hidden="true"><path d="M12 2a10 10 0 1 0 0 20 10 10 0 0 0 0-20zm6.9 6h-2.9a15 15 0 0 0-1.4-3.6A8 8 0 0 1 18.9 8zM12 4c.8 1.2 1.5 2.5 1.9 4h-3.8c.4-1.5 1.1-2.8 1.9-4zM4.3 14a8 8 0 0 1 0-4h3.4a16 16 0 0 0 0 4zm.8 2h2.9c.3 1.3.8 2.5 1.4 3.6A8 8 0 0 1 5.1 16zM8 8H5.1a8 8 0 0 1 4.3-3.6C8.8 5.5 8.3 6.7 8 8zm4 12c-.8-1.2-1.5-2.5-1.9-4h3.8c-.4 1.5-1.1 2.8-1.9 4zm2.3-6H9.7a14 14 0 0 1 0-4h4.6a14 14 0 0 1 0 4zm.3 5.6c.6-1.1 1.1-2.3 1.4-3.6h2.9a8 8 0 0 1-4.3 3.6zm1.7-5.6a16 16 0 0 0 0-4h3.4a8 8 0 0 1 0 4z"/></svg>
        <span>www.<span class="highlight">websitename</span>.com</span>
      </li>
    </ul>
    <address class="address">
      421, Address line goes here<br>
      45452,Country Name
    </address>
  </section>
</main>
</body>
</html>
```